Business Card Design

New business card design

Target Market(s)

Residential & Commercial Property Managers

Industry/Entity Type

Plumbing Services

Contact Information for Business Card

Name - Rowan Keddle, title - Director, Phone Number - 0431 286 517, email - rowan@tbk-plumbing.com.au, Company ABN - 73 215 904 386,

Font styles to use
Sans Serif

Colors
0054AA
0677BA
7BADD7
CADEEF
E8F1F8

```html
<!DOCTYPE html>
<html lang="en">
<head>
<meta charset="utf-8">
<title>TBK Plumbing Services – Business Card</title>
<link rel="stylesheet" href="https://fonts.googleapis.com/css2?family=Montserrat:wght@300;400;700&display=swap">
<style>
  :root {
    --backdrop: #232323;
    --card: #ffffff;
    --brand-blue: #2ba8e0;
    --navy: #1d2228;
    --ink: #1f252b;
    --light-text: #ffffff;
  }
  * { margin: 0; padding: 0; box-sizing: border-box; }
  html, body { width: 1200px; height: 780px; overflow: hidden; }
  body {
    background: var(--backdrop);
    font-family: "Montserrat", sans-serif;
    position: relative;
  }
  .card {
    position: absolute;
    top: 240px;
    width: 520px;
    height: 300px;
    background: var(--card);
    border-radius: 22px;
    overflow: hidden;
    box-shadow: 0 4px 0 var(--brand-blue), 0 18px 40px rgba(0,0,0,0.55);
  }
  .card--front { left: 50px; }
  .card--back  { left: 630px; }

  .brand {
    display: flex;
    align-items: center;
    gap: 12px;
    color: var(--ink);
    font-weight: 400;
    letter-spacing: 0.02em;
    white-space: nowrap;
  }
  .brand__mark {
    border-radius: 50%;
    background: var(--brand-blue);
    flex: none;
  }
  .card--front .brand {
    position: absolute;
    inset: 0;
    justify-content: center;
    font-size: 30px;
  }
  .card--front .brand__mark { width: 26px; height: 26px; }

  .card--back .brand {
    position: absolute;
    left: 32px;
    top: 92px;
    font-size: 19px;
  }
  .card--back .brand__mark { width: 16px; height: 16px; }

  .wave {
    position: absolute;
    inset: 0;
    width: 520px;
    height: 300px;
  }

  .name-tab {
    position: absolute;
    right: 0;
    top: 18px;
    width: 16px;
    height: 44px;
    background: var(--brand-blue);
  }
  .person {
    position: absolute;
    right: 30px;
    top: 20px;
    text-align: right;
  }
  .person__name {
    color: var(--brand-blue);
    font-weight: 700;
    font-size: 22px;
    line-height: 1.1;
  }
  .person__title {
    color: var(--ink);
    font-weight: 400;
    font-size: 14px;
    margin-top: 2px;
  }

  .contact {
    position: absolute;
    right: 22px;
    top: 140px;
    text-align: right;
    color: var(--light-text);
    font-weight: 300;
    font-size: 14px;
    line-height: 1.4;
    white-space: nowrap;
  }
  .contact__abn { margin-bottom: 30px; }
  .contact__line {
    display: flex;
    justify-content: flex-end;
    align-items: center;
    gap: 7px;
  }
  .contact__icon { width: 14px; height: 14px; flex: none; }
</style>
</head>
<body>

  <section class="card card--front" aria-label="Card front">
    <div class="brand"><span class="brand__mark"></span>TBK Plumbing Services</div>
  </section>

  <section class="card card--back" aria-label="Card back">
    <svg class="wave" viewBox="0 0 520 300" aria-hidden="true">
      <path d="M470,62 C320,66 260,262 0,258 L0,300 L520,300 L520,62 Z" fill="var(--brand-blue)"/>
      <path d="M488,64 C335,70 275,278 0,280" fill="none" stroke="#ffffff" stroke-width="5"/>
      <path d="M520,72 C360,76 300,290 40,300 L520,300 Z" fill="var(--navy)"/>
      <path d="M520,68 C352,72 290,286 30,300" fill="none" stroke="#ffffff" stroke-width="4"/>
    </svg>

    <div class="brand"><span class="brand__mark"></span>TBK Plumbing Services</div>

    <span class="name-tab"></span>
    <div class="person">
      <div class="person__name">Rowan Keddle</div>
      <div class="person__title">Director</div>
    </div>

    <div class="contact">
      <div class="contact__abn">Company ABN<br>- 73 215 904 386</div>
      <div class="contact__line">0431 286 517
        <svg class="contact__icon" viewBox="0 0 24 24" aria-hidden="true"><path fill="var(--brand-blue)" d="M6.6 10.8a15.2 15.2 0 0 0 6.6 6.6l2.2-2.2a1 1 0 0 1 1-.25 11.4 11.4 0 0 0 3.6.57 1 1 0 0 1 1 1V20a1 1 0 0 1-1 1A17 17 0 0 1 3 4a1 1 0 0 1 1-1h3.5a1 1 0 0 1 1 1c0 1.25.2 2.450.57 3.57a1 1 0 0 1-.25 1z"/></svg>
      </div>
      <div class="contact__line">rowan@tbk-plumbing.com.au
        <svg class="contact__icon" viewBox="0 0 24 24" aria-hidden="true"><rect x="2" y="5" width="20" height="14" rx="2" fill="var(--brand-blue)"/><path d="M3 6l9 7 9-7" fill="none" stroke="var(--navy)" stroke-width="1.8"/></svg>
      </div>
    </div>
  </section>

</body>
</html>
```